Stationery Design Project for Mindwell Care Clinic

I would like you to design a letterhead and appt cards and letterhead. i have attached our current brochure so that you can see the kind of clinic that we are - for some context.

Generally our letters will go to General Practitioners.
Appt cards to clients. The text can stay the same as current documents as attached but the design obviously needs to be totally changed.

We are a psychology clinic with several psychologists that work for me. THe psychologists come and go so I am not wanting to list their names on the stationary.

In terms of letterhead my name (dr marion tasker) needs to be on there..eg dr marion tasker & associates.

With envelopes we need to be discrete therefore we simply have MCC & our address.

Everything goes under the banner of Mindwell Care Clinic Pty Ltd.

I would like it to be consistent in theme/colours with the logo you designed and our website which has just gone live www.mindwellcareclinic.com.au

Target Market(s)

General practitioners, potential referrers usually in the medical/health field,

Industry/Entity Type

Clinic

Requirements
Must have
• Logo

Address Suite 4, 2287 Larkmoor Rd, Larkmoor West 3172
P 9362 5184 F 9362 5190 E info@mindwellcareclinic.com.au
W mindwellcareclinic.com.au

Mindwell Care Clinic Pty Ltd (small font)
ABN (ill need to provide this) (small font)
Nice to have
• I really like in my website how the colours are graded in the banners...I think this gives a softer feel...so if something like that would look good in our stationary then please use that kind of technique too...but you guys are the experts.

```html
<!DOCTYPE html>
<html lang="en">
<head>
<meta charset="utf-8">
<title>Mindwell Care Clinic – Appointment Card</title>
<link href="https://fonts.googleapis.com/css2?family=Lato:ital,wght@0,300;0,400;1,400&display=swap" rel="stylesheet">
<style>
  :root {
    --page-bg: #d9d9d7;
    --card-front: #dfdfc8;
    --card-back: #f1f1ef;
    --ink: #4a4a48;
    --ink-soft: #7d7d78;
    --rule: #9a9a96;
    --teal: #3f8f8a;
    --teal-light: #6fb0b3;
    --sky: #86b9c2;
    --slate: #8b9ba6;
    --green: #5f9a7a;
    --olive: #b7b58c;
    --mark: #c9c9c0;
  }
  * { box-sizing: border-box; margin: 0; padding: 0; }
  html, body { width: 1200px; height: 747px; overflow: hidden; }
  body {
    background: var(--page-bg);
    font-family: "Lato", sans-serif;
    color: var(--ink);
    position: relative;
  }
  .card {
    position: absolute;
    top: 93px;
    width: 340px;
    height: 560px;
    overflow: hidden;
  }
  .card--front { left: 220px; background: var(--card-front); }
  .card--back { left: 640px; background: var(--card-back); }

  /* Front: landscape layout turned on its side */
  .front-face {
    position: absolute;
    left: -110px;
    top: 110px;
    width: 560px;
    height: 340px;
    transform: rotate(-90deg);
  }
  .band { position: absolute; left: 0; right: 0; display: flex; }
  .band span { flex: 1; }
  .front-face .band--edge { top: 0; height: 10px; }
  .front-face .band--base { bottom: 0; height: 30px; }
  .c-teal { background: var(--teal); }
  .c-teal-light { background: var(--teal-light); }
  .c-sky { background: var(--sky); }
  .c-slate { background: var(--slate); }
  .c-green { background: var(--green); }
  .c-olive { background: var(--olive); }

  .brand {
    position: absolute;
    left: 34px;
    top: 38px;
    display: flex;
    align-items: flex-start;
    gap: 22px;
  }
  .brand-dot {
    width: 70px; height: 70px;
    border-radius: 50%;
    background: var(--mark);
    margin-top: 4px;
  }
  .brand-name {
    font-weight: 300;
    font-size: 25px;
    line-height: 30px;
    letter-spacing: 7px;
    text-transform: uppercase;
    color: var(--ink-soft);
  }
  .contacts {
    position: absolute;
    left: 34px;
    bottom: 78px;
    list-style: none;
    font-size: 17px;
    line-height: 25px;
  }
  .contacts b { display: inline-block; width: 20px; font-weight: 400; }
  .address {
    position: absolute;
    right: 34px;
    bottom: 46px;
    font-style: normal;
    font-size: 17px;
    line-height: 25px;
  }

  /* Back */
  .card--back .band { height: 14px; }
  .card--back .band--top { top: 0; }
  .card--back .band--bottom { bottom: 0; }
  .back-face { position: absolute; inset: 36px 28px 30px 28px; }
  .field-title { font-size: 17px; margin-bottom: 6px; }
  .fill-line { border-bottom: 1px solid var(--rule); height: 18px; margin-bottom: 18px; }
  .appt { margin-bottom: 16px; }
  .appt-row { display: flex; align-items: flex-end; font-size: 12px; text-transform: uppercase; margin-bottom: 10px; }
  .appt-row .label { width: 44px; }
  .appt-row .line { flex: 1; border-bottom: 1px solid var(--rule); height: 12px; }
  .appt-row .ampm { margin-left: 8px; text-transform: none; font-size: 13px; }
  .company { font-size: 17px; line-height: 21px; margin-top: 20px; }
  .notice { font-style: italic; font-size: 15px; line-height: 19px; margin-top: 22px; }
</style>
</head>
<body>
  <section class="card card--front" aria-label="Card front">
    <div class="front-face">
      <div class="band band--edge">
        <span class="c-green"></span><span class="c-teal-light"></span><span class="c-sky"></span><span class="c-slate"></span><span class="c-teal"></span>
      </div>
      <div class="brand">
        <div class="brand-dot"></div>
        <h1 class="brand-name">Mindwell<br>Care<br>Clinic</h1>
      </div>
      <ul class="contacts">
        <li><b>t</b> 9362 5184</li>
        <li><b>f</b> 9362 5190</li>
        <li><b>e</b> info@mindwellcareclinic.com.au</li>
      </ul>
      <address class="address">
        Suite 4, 2287 Larkmoor Rd,<br>
        Larkmoor West 3172<br>
        mindwellcareclinic.com.au
      </address>
      <div class="band band--base">
        <span class="c-green"></span><span class="c-sky"></span><span class="c-teal-light"></span><span class="c-teal"></span><span class="c-slate"></span><span class="c-teal"></span>
      </div>
    </div>
  </section>

  <section class="card card--back" aria-label="Card back">
    <div class="band band--top">
      <span class="c-olive"></span><span class="c-teal"></span><span class="c-green"></span>
    </div>
    <div class="back-face">
      <p class="field-title">Your psychologist:</p>
      <div class="fill-line"></div>
      <p class="field-title">Your appointments:</p>
      <div class="appt">
        <div class="appt-row"><span class="label">Date</span><span class="line"></span></div>
        <div class="appt-row"><span class="label">Time</span><span class="line"></span><span class="ampm">AM | PM</span></div>
      </div>
      <div class="appt">
        <div class="appt-row"><span class="label">Date</span><span class="line"></span></div>
        <div class="appt-row"><span class="label">Time</span><span class="line"></span><span class="ampm">AM | PM</span></div>
      </div>
      <div class="appt">
        <div class="appt-row"><span class="label">Date</span><span class="line"></span></div>
        <div class="appt-row"><span class="label">Time</span><span class="line"></span><span class="ampm">AM | PM</span></div>
      </div>
      <div class="appt">
        <div class="appt-row"><span class="label">Date</span><span class="line"></span></div>
        <div class="appt-row"><span class="label">Time</span><span class="line"></span><span class="ampm">AM | PM</span></div>
      </div>
      <p class="company">Mindwell Care Clinic Pty Ltd<br>ABN 1234567</p>
      <p class="notice">Please note fees will be charged for missed appointments without 48 hours notice.</p>
    </div>
    <div class="band band--bottom">
      <span class="c-olive"></span><span class="c-teal"></span><span class="c-green"></span>
    </div>
  </section>
</body>
</html>
```